Northfield Builders Guild Business card

We are looking for a new business card design with photo included.
Our business is a nonprofit construction contractor membership organization. We offer business education, assist with business setup and licensing, provide safety training, and provide a member directory.
URL: www.builderslinkguild.org
Color code:
CMYK: 0 cyan, 42 magenta, 100 yellow, 0 black for Print.
Hexidecimal: #FF9900
RGB: R 255; G 153; B 0

```html
<!DOCTYPE html>
<html lang="en">
<head>
<meta charset="utf-8">
<title>Northfield Builders Guild Business Card</title>
<link rel="stylesheet" href="https://fonts.googleapis.com/css2?family=Open+Sans:wght@400;600;700;800&family=Michroma&display=swap">
<style>
  :root {
    --brand-orange: #f7971e;
    --ink-dark: #333436;
    --ink-body: #1f1f1f;
    --card-white: #ffffff;
    --table-grey: #e4e1de;
  }
  * { margin: 0; padding: 0; box-sizing: border-box; }
  html, body { width: 1200px; height: 997px; overflow: hidden; }
  body {
    background: var(--table-grey);
    font-family: "Open Sans", sans-serif;
    position: relative;
  }
  .card {
    position: absolute;
    width: 700px;
    height: 400px;
    background: var(--card-white);
    box-shadow: 0 6px 18px rgba(0,0,0,0.12);
    overflow: hidden;
  }
  .card-front { left: 150px; top: 58px; }
  .card-back  { left: 350px; top: 539px; }

  .wordmark {
    position: absolute;
    display: flex;
    align-items: center;
    gap: 10px;
  }
  .wordmark-square {
    width: 22px; height: 22px;
    background: var(--brand-orange);
    flex: none;
  }
  .wordmark-name {
    font-family: "Open Sans", sans-serif;
    font-weight: 800;
    color: var(--ink-dark);
    font-size: 27px;
    line-height: 1.05;
    text-transform: uppercase;
    letter-spacing: 0.5px;
  }
  .card-front .wordmark { left: 215px; top: 92px; }
  .card-back .wordmark { right: 48px; top: 58px; }

  .url-band {
    position: absolute;
    left: 0; right: 0;
    top: 220px;
    height: 46px;
    background: var(--brand-orange);
    display: flex;
    align-items: center;
    justify-content: center;
  }
  .url-band-text {
    color: var(--card-white);
    font-size: 19px;
    letter-spacing: 6px;
  }

  .holder {
    position: absolute;
    left: 60px;
    top: 170px;
  }
  .holder-name {
    font-family: "Michroma", sans-serif;
    color: var(--brand-orange);
    font-size: 19px;
    letter-spacing: 4px;
    text-transform: uppercase;
  }
  .holder-title {
    font-size: 12px;
    color: var(--ink-body);
    margin-top: 2px;
    margin-left: 14px;
  }
  .contact-list {
    position: absolute;
    left: 74px;
    top: 248px;
    list-style: none;
  }
  .contact-item {
    display: flex;
    align-items: flex-start;
    gap: 12px;
    font-size: 14px;
    color: var(--ink-body);
    line-height: 1.25;
    margin-bottom: 8px;
  }
  .contact-icon {
    width: 20px; height: 20px;
    flex: none;
    background: var(--brand-orange);
    border-radius: 3px;
    display: flex;
    align-items: center;
    justify-content: center;
  }
  .contact-icon svg { width: 14px; height: 14px; }
</style>
</head>
<body>

  <section class="card card-front">
    <div class="wordmark">
      <span class="wordmark-square"></span>
      <span class="wordmark-name">Northfield<br>Builders Guild</span>
    </div>
    <div class="url-band">
      <span class="url-band-text">www.builderslinkguild.org</span>
    </div>
  </section>

  <section class="card card-back">
    <div class="wordmark">
      <span class="wordmark-square"></span>
      <span class="wordmark-name">Northfield<br>Builders Guild</span>
    </div>

    <div class="holder">
      <p class="holder-name">Daniel Reyes</p>
      <p class="holder-title">CEO/Managing Director</p>
    </div>

    <ul class="contact-list">
      <li class="contact-item">
        <span class="contact-icon"><svg viewBox="0 0 16 16"><path d="M4 2 L6.5 2 L7.5 5 L6 6.3 C6.8 8 8 9.2 9.7 10 L11 8.5 L14 9.5 L14 12 C14 13 13 14 12 14 C6.5 13.6 2.4 9.5 2 4 C2 3 3 2 4 2 Z" fill="#fff"/></svg></span>
        <span>555-014-2288</span>
      </li>
      <li class="contact-item">
        <span class="contact-icon"><svg viewBox="0 0 16 16"><path d="M8 2 L14.5 8 L12.5 8 L12.5 14 L9.5 14 L9.5 10 L6.5 10 L6.5 14 L3.5 14 L3.5 8 L1.5 8 Z" fill="#fff"/></svg></span>
        <span>555-014-2289</span>
      </li>
      <li class="contact-item">
        <span class="contact-icon"><svg viewBox="0 0 16 16"><rect x="2" y="4" width="12" height="8.5" fill="none" stroke="#fff" stroke-width="1.5"/><path d="M2 4 L8 9 L14 4" fill="none" stroke="#fff" stroke-width="1.5"/></svg></span>
        <span>dreyes@builderslinkguild.org</span>
      </li>
      <li class="contact-item">
        <span class="contact-icon"><svg viewBox="0 0 16 16"><circle cx="8" cy="8" r="6" fill="none" stroke="#fff" stroke-width="1.3"/><ellipse cx="8" cy="8" rx="2.6" ry="6" fill="none" stroke="#fff" stroke-width="1.1"/><path d="M2 8 H14" stroke="#fff" stroke-width="1.1"/></svg></span>
        <span>www.builderslinkguild.org</span>
      </li>
      <li class="contact-item">
        <span class="contact-icon"><svg viewBox="0 0 16 16"><path d="M8 15 C5 11 3.5 8.5 3.5 6.3 A4.5 4.5 0 0 1 12.5 6.3 C12.5 8.5 11 11 8 15 Z" fill="#fff"/><circle cx="8" cy="6.3" r="1.7" fill="#f7971e"/></svg></span>
        <span>118 Harbor Lane NW Suite 210, Northfield<br>Mi 49012</span>
      </li>
    </ul>
  </section>

</body>
</html>
```